Sun Veil Custom Spray Tanning Studio

I have attached most of the information that I would like in my brochure. However, I would like the brochure to be more elegant and professional. I am no longer offering mobile tanning, however, I will be located at: 418 W Harlow Lane, Myrtle Beach, SC 29577. 843-555-0172 and I am by appointment only.

Reason: I found designs that I like, however: Spelling and grammar is critical. Please make sure that every word is spelled correctly. I am also changing my colors with my new business cards.

Target Market(s)

My clients have an average to above average income. They are health conscience and take good care of themselves. Into high end quality work and willing to pay for it.

Industry/Entity Type

It Professional

Font styles to use
Serif
Decorative
Script

Requirements
Must have
• Correct Spelling and grammar are a must. Please make sure everything is spelled correctly, punctuated properly and words are used exactly like I have it my brochure.
Nice to have
• Elegant and Classy
Should not have
• Nothing to do with Mobile Tanning.
On the front, I prefer the wording.... Call and Make your appointments at (843)555-0172. Visit us online at www.sunveiltan.com or email me at marla@sunveiltan.com

```html
<!DOCTYPE html>
<html lang="en">
<head>
<meta charset="utf-8">
<title>Sun Veil Spray Tanning Brochure – Inner</title>
<link rel="stylesheet" href="https://fonts.googleapis.com/css2?family=Advent+Pro:wght@100;200;300;400&family=Lobster&family=Roboto:wght@400&display=swap">
<style>
  :root {
    --sheet: #ffffff;
    --ink: #111111;
    --gold: #e6bf45;
    --gold-deep: #c9a022;
    --cream: #f1e2bd;
    --body-text: #d9bf92;
    --panel-dark: rgba(70, 22, 6, 0.88);
    --brown-top: #2a0502;
    --brown-mid: #8a5a30;
    --sand: #c8a468;
    --water-light: #e7b94c;
    --water-deep: #b07d1c;
  }
  * { box-sizing: border-box; margin: 0; padding: 0; }
  html, body { width: 1200px; height: 965px; overflow: hidden; background: var(--sheet); }
  .sheet { position: relative; width: 1200px; height: 965px; font-family: "Advent Pro", sans-serif; }
  .sheet-title { position: absolute; left: 24px; top: 16px; font: 400 15px "Roboto", sans-serif; color: var(--ink); }
  .sheet-label { position: absolute; left: 0; width: 1206px; top: 916px; text-align: center; font: 400 16px "Roboto", sans-serif; color: var(--ink); }
  .fold { position: absolute; top: 58px; height: 864px; border-left: 1.5px dashed #222; z-index: 2; }
  .fold-1 { left: 405px; } .fold-2 { left: 790px; }

  .spread { position: absolute; left: 24px; top: 84px; width: 1149px; height: 812px; border: 1.5px solid #111; overflow: hidden; }
  .water { position: absolute; left: 0; top: 0; width: 766px; height: 789px;
    background: radial-gradient(ellipse at 30% 20%, var(--water-light), var(--water-deep) 70%); }
  .model-photo { position: absolute; left: 355px; top: 0; width: 411px; height: 789px;
    background: linear-gradient(180deg, #d9ae3c 0%, #a37c42 30%, #8c6a3e 60%, #b48d45 100%); }
  .base-band { position: absolute; left: 0; bottom: 0; width: 766px; height: 22px;
    background: linear-gradient(90deg, #5a1e10 0%, #b99461 30%, #d4b27a 55%, #b08a58 80%, #5a1e10 100%); }
  .right-panel { position: absolute; left: 766px; top: 0; width: 383px; height: 100%;
    background: linear-gradient(180deg, var(--brown-top) 0%, #5c2e16 25%, var(--brown-mid) 45%, var(--sand) 72%, #8e6a3e 88%, #3c1406 100%); }

  .info-panel { position: absolute; left: 28px; top: 28px; width: 327px; height: 735px; background: var(--panel-dark); padding: 30px 32px 0; color: var(--body-text); }
  .info-heading { text-align: center; color: var(--cream); font-weight: 200; line-height: 1; white-space: nowrap; }
  .info-heading .lead { font-size: 24px; letter-spacing: 0.5px; }
  .brand-script { font-family: "Lobster", cursive; color: var(--gold); font-size: 36px; letter-spacing: 0.5px; }
  .info-heading .sub { display: block; font-size: 32px; letter-spacing: 0; margin-top: 4px; transform: scaleX(0.92); }
  .body-copy { font-size: 11.8px; font-weight: 300; line-height: 14.8px; text-align: justify; letter-spacing: 0.6px; margin-top: 12px; }
  .body-copy + .body-copy { margin-top: 13px; }
  .divider { border: 0; border-top: 1px solid var(--cream); margin: 16px 0 12px; opacity: 0.85; }
  .section-title { font-family: "Lobster", cursive; color: var(--gold); font-size: 32px; text-align: center; line-height: 1; font-weight: 400; }

  .tagline { position: absolute; left: 0; top: 128px; width: 100%; text-align: center; font-weight: 100; line-height: 0.9; }
  .tagline span { display: block; transform: scale(0.78, 1.2); }
  .tagline .line-1 { color: var(--cream); font-size: 52px; }
  .tagline .line-2 { color: var(--cream); font-size: 80px; margin-top: 12px; }
  .tagline .line-2 small { font-size: 40px; }
  .tagline .line-3 { color: var(--gold-deep); font-size: 80px; margin-top: 8px; }
  .product-photo { position: absolute; left: 55px; top: 360px; width: 275px; height: 300px; border-radius: 8px;
    background: linear-gradient(180deg, #f4f1ec 0%, #d9d3c8 70%, rgba(200,164,104,0) 100%); }
</style>
</head>
<body>
<div class="sheet">
  <p class="sheet-title">Sun Veil Spray Tanning Brochure Design02_Inner</p>
  <div class="fold fold-1"></div>
  <div class="fold fold-2"></div>

  <div class="spread">
    <div class="water" role="img" aria-label="Sunlit golden water texture"></div>
    <div class="model-photo" role="img" aria-label="Tanned woman in a striped bikini and straw hat lying in shallow water"></div>
    <div class="base-band"></div>

    <section class="info-panel">
      <h2 class="info-heading">
        <span class="lead">Use </span><span class="brand-script">Sun Veil</span><span class="lead"> for</span>
        <span class="sub">healthy, radiant skin</span>
      </h2>
      <p class="body-copy">Sun Veil proudly offers a leading spray tanning product that will indulge your skin in a safe and effective way. It achieves a natural result without sun damage or premature aging in less than 10 minutes. All sessions include our special mixture of antioxidants and pure botanicals that leave your skin radiant with a sun-kissed glow that can last up to 7-10 days.</p>
      <p class="body-copy">Our equipment is the most technologically advanced system on the market. It is the only system that delivers high-end beauty treatments along with sunless tanning, all in one unique system. In addition, it is the only sunless tanning company to achieve "carbon neutral" status and proven to be the fastest, most consistent, fully computerized system on the market. This ensures the highest quality true "spray and go," which will allow our technicians to provide top-of-the-line service.</p>
      <hr class="divider">
      <h3 class="section-title">How it works</h3>
      <p class="body-copy">Our sunless tan is just like the one you achieve after hours of lying on the beach, and just like the real tan, it will fade. Why? Every day, millions of dead skin cells are worn away from the surface of your skin. In fact, as the dead cells are worn away, so will the tan. Fading of this kind applies to all tans, both sunless and real. To maintain your tan, Sun Veil recommends tanning 2-3 times a month.</p>
      <p class="body-copy">Following a skincare regimen is very important for your spray tan. Twice a day, hydrate your skin and drink plenty of water. Our skincare products will help you enjoy a beautiful, long-lasting tan.</p>
    </section>

    <section class="right-panel">
      <h2 class="tagline">
        <span class="line-1">Skincare from</span>
        <span class="line-2">sunup <small>to</small></span>
        <span class="line-3">sundown</span>
      </h2>
      <div class="product-photo" role="img" aria-label="Group of white skincare bottles and a jar with reflection"></div>
    </section>
  </div>

  <p class="sheet-label">Inner</p>
</div>
</body>
</html>
```